Business Card Design

Hi I need a business card designed, we already have the business name logo artwork and would like some concept ideas for the Bus Card layout.
On the back of the card i want to include the products and services that we offer.
We are a Plastics Sheeting manufacture based in Perth Australia.

                                       

We need a BC design for a company called Tarvo Plastics based in Perth Australia.

We supply from DIY to Trade & Industrial  Engineering Markets.

We specialise in:

·         Cut to size panels  (all shapes and sizes)

·         Plastics fabrication & Welding

·         Custom Designs

·         Plastic Repairs

·         PVC Pipe Slotting & PVC Pipe Threading

·         Supplier of all types of engineering plastics and profiles.

Including:           Acrylic / Clarvene

                               Polycarbonate / Dorvil

                               Prismatic Light Diffuser

                               Vantrib

                               HDPE / UHMWPE

                               PVC / PVC Foam

                               Nylon

                               HIPS

```html
<!DOCTYPE html>
<html lang="en">
<head>
<meta charset="utf-8">
<title>Tarvo Plastics – Business Card</title>
<link rel="stylesheet" href="https://fonts.googleapis.com/css2?family=Arimo:wght@400;700&display=swap">
<style>
  :root {
    --navy: #15295e;
    --navy-text: #1c2f66;
    --link-blue: #2a8fd0;
    --white: #ffffff;
    --page: #e9e7e4;
  }
  * { box-sizing: border-box; margin: 0; padding: 0; }
  html, body {
    width: 1200px; height: 631px; overflow: hidden;
    background: var(--page);
    font-family: "Arimo", Arial, sans-serif;
  }
  .sheet {
    position: relative; width: 1200px; height: 631px;
    display: flex; align-items: center; justify-content: center; gap: 40px;
  }
  .card {
    position: relative; width: 540px; height: 330px; overflow: hidden;
    box-shadow: 0 4px 14px rgba(0,0,0,0.18);
  }

  /* Back */
  .card--back { background: var(--navy); color: var(--white); }
  .card--back .brand {
    position: absolute; top: 24px; right: 30px;
    font-size: 32px; font-weight: 700; color: var(--white);
  }
  .intro { position: absolute; top: 92px; left: 26px; font-size: 11px; }
  .services { position: absolute; top: 124px; left: 26px; font-size: 11px; line-height: 17px; }
  .services h3, .materials h3 { font-size: 11px; font-weight: 700; }
  .services ul { list-style: none; }
  .services li::before { content: "• "; }
  .materials { position: absolute; top: 124px; left: 360px; font-size: 11px; line-height: 17px; font-weight: 700; }
  .materials h3 { font-style: italic; }
  .materials ul { list-style: none; }

  /* Front */
  .card--front { background: var(--white); color: var(--navy-text); }
  .card--front .brand {
    position: absolute; top: 82px; left: 34px;
    font-size: 48px; font-weight: 700; color: var(--navy);
    letter-spacing: -0.5px;
  }
  .person { position: absolute; top: 26px; left: 318px; font-size: 18px; line-height: 22px; }
  .person .name { font-weight: 700; }
  .person .role { display: block; font-weight: 700; font-size: 17px; margin-left: 14px; }
  .contact { position: absolute; top: 180px; left: 34px; font-size: 17px; line-height: 21px; }
  .contact strong { font-weight: 700; }
  .contact a { color: var(--link-blue); text-decoration: none; }
  .contact .legal { font-size: 9px; line-height: 18px; letter-spacing: 0.2px; }
</style>
</head>
<body>
<main class="sheet">
  <section class="card card--back" aria-label="Card back">
    <div class="brand">Tarvo Plastics</div>
    <p class="intro">We supply from DIY to Trade &amp; Industrial&nbsp; Engineering Markets.</p>
    <div class="services">
      <h3>We specialise in:</h3>
      <ul>
        <li>Cut to size panels&nbsp; (all shapes and sizes)</li>
        <li>Plastics fabrication &amp; Welding</li>
        <li>Custom Designs</li>
        <li>Plastic Repairs</li>
        <li>PVC Pipe Slotting &amp; PVC Pipe Threading</li>
        <li>Supplier of all types of engineering plastics and profiles.</li>
      </ul>
    </div>
    <div class="materials">
      <h3>Including</h3>
      <ul>
        <li>Acrylic / Clarvene</li>
        <li>Polycarbonate / Dorvil</li>
        <li>Prismatic Light Diffuser</li>
        <li>Vantrib</li>
        <li>HDPE / UHMWPE</li>
        <li>PVC / PVC Foam</li>
        <li>Nylon</li>
        <li>HIPS</li>
      </ul>
    </div>
  </section>

  <section class="card card--front" aria-label="Card front">
    <div class="brand">Tarvo Plastics</div>
    <p class="person"><span class="name">Name</span>| 1234 123 123<span class="role">Manager</span></p>
    <div class="contact">
      <p>Unit 4/18 Brennock Way Kelmarsh WA 6158</p>
      <p>Ph: <strong>08 9400 3117</strong>&nbsp; Fax: <strong>08 9400 3118</strong></p>
      <p>E: <a href="mailto:sales@tarvoplastics.com.au">sales@tarvoplastics.com.au</a></p>
      <p>PO Box 2284 Kelmarsh DC WA 6972</p>
      <p class="legal">ORLENBY HOLDINGS Pty Ltd T/A Tarvo Plastics ABN: TBA</p>
    </div>
  </section>
</main>
</body>
</html>
```